Bramblewood Card Company Business Cards

We are a trading card store with Glimmorax, sports and other TCG cards, we need a business card design that encompasses a clean cut, modern style with a retro flare. website is bramblewoodcardco.com for reference. Can utilize a comic book era feel or a more modern outdoor feel to utilize the "Pacific Northwest" elements of tress, mountains, etc.

Industry/Entity Type

Trading cards and collectibles

Contact Information for Business Card

business name, email address, phone number, name, owner job title

Font styles to use
Sans Serif

```html
<!DOCTYPE html>
<html lang="en">
<head>
<meta charset="utf-8">
<title>Bramblewood Card Company – Business Card</title>
<link rel="stylesheet" href="https://fonts.googleapis.com/css2?family=Montserrat:wght@400;500;700;800&display=swap">
<style>
  :root {
    --bg: #d9d9d8;
    --card: #1e1e1f;
    --card-deep: #151516;
    --accent: #1fb8dc;
    --text: #f2f2f2;
    --muted: #8a8a8c;
    --rule: #4a4a4c;
  }
  * { box-sizing: border-box; margin: 0; padding: 0; }
  html, body {
    width: 1200px; height: 801px; overflow: hidden;
    background: radial-gradient(ellipse at 40% 35%, #ececeb 0%, var(--bg) 75%);
    font-family: "Montserrat", sans-serif;
  }
  .sheet {
    width: 1200px; height: 801px;
    display: flex; align-items: center; justify-content: center; gap: 40px;
  }
  .card {
    position: relative;
    width: 540px; height: 309px;
    background: var(--card);
    border-bottom: 5px solid var(--accent);
    border-left: 2px solid var(--accent);
    overflow: hidden;
  }
  /* front */
  .card-front { display: flex; align-items: center; }
  .brand-block {
    width: 250px; height: 100%;
    display: flex; flex-direction: column; align-items: center; justify-content: center;
    gap: 14px; padding: 0 24px;
  }
  .brand-dot {
    width: 22px; height: 22px; border-radius: 50%; background: var(--accent);
  }
  .brand-name {
    color: var(--text); font-weight: 800; font-size: 21px; line-height: 1.15;
    text-transform: uppercase; text-align: center; letter-spacing: 0.5px;
  }
  .divider {
    width: 1px; height: 150px; background: var(--rule);
  }
  .contact-block { padding-left: 30px; color: var(--text); }
  .person-name {
    color: var(--accent); font-weight: 800; font-size: 24px;
    text-transform: uppercase; letter-spacing: 0.5px;
  }
  .person-title { font-size: 13px; margin-top: 2px; }
  .address { font-size: 12px; line-height: 1.45; margin-top: 16px; }
  .contact-list { list-style: none; margin-top: 14px; font-size: 12px; }
  .contact-list li { display: flex; align-items: center; gap: 8px; line-height: 1.75; }
  .contact-list svg { width: 12px; height: 12px; flex: none; }
  .web-domain { color: var(--accent); }
  /* back */
  .pattern-field {
    position: absolute; inset: 0;
    background: linear-gradient(115deg, var(--card-deep) 0%, #2a2a2b 55%, #5d5d5f 100%);
  }
  .back-mark {
    position: absolute; right: 70px; top: 150px;
    display: flex; align-items: center; gap: 8px;
  }
  .back-mark .brand-dot { width: 12px; height: 12px; }
  .back-mark .brand-name { font-size: 11px; text-align: left; }
</style>
</head>
<body>
<main class="sheet">
  <section class="card card-front" aria-label="Business card front">
    <div class="brand-block">
      <span class="brand-dot"></span>
      <p class="brand-name">Bramblewood<br>Card Company</p>
    </div>
    <div class="divider"></div>
    <div class="contact-block">
      <h1 class="person-name">Dorian Vale</h1>
      <p class="person-title">CEO/Founder</p>
      <p class="address">P.O. Box 3817 Alder Lane<br>Fernvale WA 5736</p>
      <ul class="contact-list">
        <li>
          <svg viewBox="0 0 12 12" aria-hidden="true"><circle cx="6" cy="6" r="6" fill="var(--accent)"/><path d="M4 3.2c.4 2.3 2 4.3 4.8 5.3l.4-1.1-1.3-.6-.6.6C6.2 7 5.2 6 4.9 5l.6-.6-.5-1.3z" fill="var(--card)"/></svg>
          (555) 314 2708
        </li>
        <li>
          <svg viewBox="0 0 12 12" aria-hidden="true"><rect x="0.5" y="2" width="11" height="8" fill="var(--accent)"/><path d="M0.5 2 6 6.5 11.5 2" fill="none" stroke="var(--card)" stroke-width="1"/></svg>
          info@bramblewoodcardco.com
        </li>
        <li>
          <svg viewBox="0 0 12 12" aria-hidden="true"><circle cx="6" cy="6" r="5.5" fill="var(--accent)"/><path d="M0.5 6h11M6 0.5v11M2 3.2h8M2 8.8h8" stroke="var(--card)" stroke-width="0.7" fill="none"/><ellipse cx="6" cy="6" rx="2.4" ry="5.5" fill="none" stroke="var(--card)" stroke-width="0.7"/></svg>
          www.<span class="web-domain">bramblewoodcardco</span>.com
        </li>
      </ul>
    </div>
  </section>

  <section class="card card-back" aria-label="Business card back">
    <div class="pattern-field" role="img" aria-label="Repeating brand emblem pattern fading from black to grey"></div>
    <div class="back-mark">
      <span class="brand-dot"></span>
      <p class="brand-name">Bramblewood<br>Card Company</p>
    </div>
  </section>
</main>
</body>
</html>
```